Fernhale Business Card Design

We are looking for a fresh business card design for our new logo. We would like a business card that is unique but friendly. We are in the window coverings business offering blinds, shutters and shades for homes.

Target Market(s)

Targeting the end-consumer

Industry/Entity Type

Business

Requirements
Must have
• Must have a dedicates space for a photo of our sales person. Must contain our new logo (attached).

```html
<!DOCTYPE html>
<html lang="en">
<head>
<meta charset="utf-8">
<title>Fernhale Business Card</title>
<link href="https://fonts.googleapis.com/css2?family=Roboto+Condensed:wght@400;700&display=swap" rel="stylesheet">
<style>
:root{
  --bg:#e9e8e4;
  --white:#fdfdfd;
  --green:#8fcb3f;
  --green-light:#9dd44a;
  --green-dark:#7dbb34;
  --grey:#8c8c8e;
  --grey-text:#7a7b7d;
  --photo-light:#e2e2e2;
  --photo-dark:#b9b9b9;
  --ink:#ffffff;
}
*{margin:0;padding:0;box-sizing:border-box}
html,body{width:1200px;height:886px;overflow:hidden;background:var(--bg)}
body{font-family:"Roboto Condensed",sans-serif;position:relative}
.card{position:absolute;top:288px;width:540px;height:310px;border-radius:4px;overflow:hidden;box-shadow:0 6px 18px rgba(0,0,0,.18)}
.card-front{left:40px;background:var(--white)}
.card-back{left:620px;background:linear-gradient(135deg,var(--green-light),var(--green-dark))}

.front-brand{position:absolute;left:34px;top:212px;display:flex;align-items:center;gap:10px}
.brand-square{width:30px;height:30px;border:2px solid var(--grey-text);border-radius:4px}
.brand-name{font-size:34px;color:var(--grey-text);font-weight:400;letter-spacing:.5px}

.front-panel{position:absolute;left:228px;top:0;right:0;bottom:0;background:linear-gradient(160deg,var(--green-light),var(--green))}
.address-band{position:absolute;left:228px;right:0;bottom:0;height:38px;background:var(--grey);color:var(--ink);font-size:15px;display:flex;align-items:center;padding-left:18px}

.photo-slot{position:absolute;left:268px;top:26px;width:128px;height:118px;border-radius:10px;border:2px solid #d7d7d7;background:linear-gradient(180deg,var(--photo-light),var(--photo-dark))}
.person{position:absolute;left:412px;top:62px;color:var(--ink)}
.person-name{font-size:20px;font-weight:700;line-height:1.1}
.person-title{font-size:15px;line-height:1.3}

.contact-list{position:absolute;left:250px;top:160px;list-style:none;color:var(--ink);font-size:14px;line-height:20px}
.contact-list li{display:flex;align-items:center;gap:8px}
.contact-list svg{width:12px;height:12px;flex:none}

.back-brand{position:absolute;right:40px;bottom:66px;text-align:right;color:var(--ink)}
.back-name{font-size:46px;font-weight:400;line-height:1}
.back-web{font-size:13px;letter-spacing:4px;margin-top:6px}
</style>
</head>
<body>
<section class="card card-front">
  <div class="front-panel"></div>
  <div class="front-brand">
    <span class="brand-square"></span>
    <span class="brand-name">Fernhale</span>
  </div>
  <div class="photo-slot" role="img" aria-label="Photo of the sales person"></div>
  <div class="person">
    <div class="person-name">DANA PRYOR</div>
    <div class="person-title">CEO/FOUNDER</div>
  </div>
  <ul class="contact-list">
    <li><svg viewBox="0 0 12 12"><path d="M2 1l2 0 1 3-1.5 1a6 6 0 0 0 3.5 3.5L8 7l3 1 0 2c0 1-1 1.5-2 1.5A9 9 0 0 1 .5 3C.5 2 1 1 2 1z" fill="#fff"/></svg>512 804 3176</li>
    <li><svg viewBox="0 0 12 12"><rect x="3" y=".5" width="6" height="11" rx="1" fill="none" stroke="#fff" stroke-width="1.2"/><circle cx="6" cy="9.5" r=".8" fill="#fff"/></svg>512 804 3190</li>
    <li><svg viewBox="0 0 12 12"><rect x="1" y="4" width="10" height="6" rx="1" fill="#fff"/><rect x="3" y="1" width="6" height="3" fill="#fff"/></svg>512 804 3205</li>
    <li><svg viewBox="0 0 12 12"><rect x="1" y="2.5" width="10" height="7" fill="none" stroke="#fff" stroke-width="1.2"/><path d="M1 2.5l5 4 5-4" fill="none" stroke="#fff" stroke-width="1.2"/></svg>hello@fernhale.com</li>
    <li><svg viewBox="0 0 12 12"><circle cx="6" cy="6" r="5" fill="none" stroke="#fff" stroke-width="1.2"/><path d="M1 6h10M6 1c-2.5 3-2.5 7 0 10M6 1c2.5 3 2.5 7 0 10" fill="none" stroke="#fff" stroke-width=".9"/></svg>www.fernhale.com</li>
  </ul>
  <div class="address-band">4120 Alder Court, Juneau, Alaska 99801</div>
</section>

<section class="card card-back">
  <div class="back-brand">
    <div class="back-name">Fernhale</div>
    <div class="back-web">www.fernhale.com</div>
  </div>
</section>
</body>
</html>
```